Update our OBGYN business card look and info

We are an OBGYN office. Our logo is nice but would like to "woman" part of the logo to be a darker color, to contrast with the flower that surrounds it. Maybe make our practice name Bloom Harbor Health more feminine. Our practice caters to women only. All providers and staff are female.

Target Market(s)

Females 16-65.

Industry/Entity Type

Business

Contact Information for Business Card

See attached upload. The ONLY CHANGE to the information is DELETE the name Paula Renwick, Midwife and REPLACE with Dora Fintelli, Midwife

Logo Text

Bloom Harbor Health Obstetrics & Gynecology

Font styles to use
Serif
Script

Colors
85cae6
0692cd
33a6d7
85abd2
f59195
eea4c8
cadf82
fac994
d3a5cc

```html
<!DOCTYPE html>
<html lang="en">
<head>
<meta charset="utf-8">
<title>Bloom Harbor Health — Business Card</title>
<link rel="stylesheet" href="https://fonts.googleapis.com/css2?family=Cinzel:wght@500&family=Arimo:wght@400;700&display=swap">
<style>
  :root {
    --bg: #eef0f1;
    --card-white: #ffffff;
    --brand-blue: #6fb9d3;
    --back-blue: #7fc3d8;
    --rule-blue: #7cc0d8;
    --ink-gray: #5e5f61;
    --band-gray: #4f5052;
    --text-dark: #3f4042;
  }
  * { margin: 0; padding: 0; box-sizing: border-box; }
  html, body { width: 1200px; height: 900px; overflow: hidden; background: var(--bg); }
  .stage { position: relative; width: 1200px; height: 900px; }
  .card {
    position: absolute; left: 280px; width: 640px; height: 366px;
    overflow: hidden; box-shadow: 0 6px 20px rgba(0,0,0,.12);
  }
  .card-front { top: 48px; background: var(--card-white); }
  .card-back { top: 470px; background: var(--back-blue); }

  .card-shape { position: absolute; inset: 0; }

  .brand { position: absolute; left: 40px; top: 58px; display: flex; align-items: center; gap: 16px; }
  .brand-mark { width: 46px; height: 46px; border-radius: 50%; background: var(--brand-blue); flex: none; }
  .brand-name { font-family: "Cinzel", serif; font-weight: 500; font-size: 17px; letter-spacing: .5px; color: var(--brand-blue); text-transform: uppercase; }
  .brand-tagline { font-family: "Arimo", sans-serif; font-weight: 700; font-size: 17px; color: var(--ink-gray); margin-top: 2px; }

  .address { position: absolute; left: 430px; top: 52px; font-family: "Arimo", sans-serif; font-size: 13px; line-height: 1.3; color: var(--text-dark); }
  .contact-list { position: absolute; left: 430px; top: 140px; list-style: none; font-family: "Arimo", sans-serif; font-size: 13px; line-height: 1.35; color: var(--text-dark); }
  .contact-list li { display: flex; align-items: center; gap: 8px; }
  .contact-list svg { width: 12px; height: 12px; flex: none; }

  .providers { position: absolute; left: 40px; top: 214px; list-style: none; font-family: "Arimo", sans-serif; font-size: 15px; line-height: 1.28; color: var(--text-dark); }
  .providers b { font-weight: 700; }

  .back-content { position: absolute; inset: 0; display: flex; flex-direction: column; align-items: center; justify-content: center; color: #fff; }
  .back-brand { display: flex; align-items: center; gap: 18px; margin-top: -30px; }
  .back-brand .brand-mark { background: #fff; width: 54px; height: 54px; }
  .back-brand .brand-name { color: #fff; font-size: 18px; }
  .back-brand .brand-tagline { color: #fff; font-weight: 400; font-size: 16px; }
  .back-web { position: absolute; bottom: 62px; font-family: "Arimo", sans-serif; font-size: 13px; letter-spacing: 1px; font-weight: 700; }
</style>
</head>
<body>
<main class="stage">
  <section class="card card-front" aria-label="Business card front">
    <svg class="card-shape" viewBox="0 0 640 366" aria-hidden="true">
      <line x1="230" y1="126" x2="640" y2="126" stroke="var(--rule-blue)" stroke-width="1.2"/>
      <path d="M0 366 C 200 352, 420 300, 640 216 L 640 366 Z" fill="var(--brand-blue)"/>
      <path d="M190 366 C 360 346, 500 300, 640 236 L 640 366 Z" fill="var(--band-gray)"/>
      <path d="M40 366 C 240 350, 440 296, 640 218" fill="none" stroke="var(--card-white)" stroke-width="0"/>
    </svg>

    <div class="brand">
      <span class="brand-mark"></span>
      <div>
        <div class="brand-name">Bloom Harbor Health</div>
        <div class="brand-tagline">Obstetrics &amp; Gynecology</div>
      </div>
    </div>

    <address class="address" style="font-style:normal">
      418 Linden Crest Road<br>Suite 3B<br>Fairhaven, GA 30455
    </address>

    <ul class="contact-list">
      <li><svg viewBox="0 0 12 12"><path d="M3 1 L5 3.5 L4 5 Q5 7 7 8 L8.5 7 L11 9 L9.5 11 Q4 10.5 1 3 Z" fill="var(--brand-blue)"/></svg>(555) 318-2047</li>
      <li><svg viewBox="0 0 12 12"><rect x="3" y="1" width="6" height="3" fill="var(--brand-blue)"/><rect x="1" y="4.5" width="10" height="4.5" rx="1" fill="var(--brand-blue)"/><rect x="3" y="8" width="6" height="3" fill="var(--brand-blue)"/></svg>(555) 318-2096</li>
      <li><svg viewBox="0 0 12 12"><rect x="1" y="2.5" width="10" height="7" fill="none" stroke="var(--brand-blue)"/><path d="M1 2.5 L6 6.5 L11 2.5" fill="none" stroke="var(--brand-blue)"/></svg>info@bloomharborhealth.com</li>
      <li><svg viewBox="0 0 12 12"><circle cx="6" cy="6" r="5" fill="none" stroke="var(--brand-blue)"/><ellipse cx="6" cy="6" rx="2.2" ry="5" fill="none" stroke="var(--brand-blue)"/><line x1="1" y1="6" x2="11" y2="6" stroke="var(--brand-blue)"/></svg>www.bloomharborhealth.com</li>
    </ul>

    <ul class="providers">
      <li><b>Marion Keltner</b>, MD</li>
      <li><b>Nadia Ostrander</b>, MD</li>
      <li><b>Lena Corvell</b>, MD</li>
      <li><b>Dora Fintelli</b>, Midwife</li>
      <li><b>Ruth Delacey</b>, Midwife</li>
    </ul>
  </section>

  <section class="card card-back" aria-label="Business card back">
    <div class="back-content">
      <div class="back-brand">
        <span class="brand-mark"></span>
        <div>
          <div class="brand-name">Bloom Harbor Health</div>
          <div class="brand-tagline">Obstetrics &amp; Gynecology</div>
        </div>
      </div>
      <div class="back-web">www.bloomharborhealth.com</div>
    </div>
  </section>
</main>
</body>
</html>
```